Stonebrace Business Card Design

The Stonebrace Co is an aggregate (crushing) equipment dealer serving Western Canadian provinces. Stonebrace is a distributor of aggregate equipment for different manufacturers.

We are looking to change and update the existing business card which has been used since the existence of the company. A copy of existing card has been attached for reference. The Stonebrace Co logo we want to remain the same and we want the green color to remain the same.

We are wanting something new with a different look. A refreshing card to show a new modern and updated look. No longer wanting to have the manufacturers on the back of the card but something more like our logo on the back of the card with a statement like "Crushing Solutions"

ideas could be:
- card can be different colors on front and back
- front or reverse of the card could possibly be the green color with the logo in black

Target Market(s)

Owners of Aggregate/Crushing companies

Contact Information for Business Card

see above

Requirements
Must have
• - logo to remain same along with same font within logo
• - green color to remain same
Nice to have
• as noted above under project description
Should not have

```html
<!DOCTYPE html>
<html lang="en">
<head>
<meta charset="utf-8">
<title>Stonebrace Co – Business Card</title>
<link href="https://fonts.googleapis.com/css2?family=Roboto:wght@400;500;700&family=Roboto+Condensed:wght@400;700&display=swap" rel="stylesheet">
<style>
  :root {
    --backdrop: #ecebe6;
    --brand-green: #8a8c0b;
    --card-white: #f4f4f2;
    --ink: #1f1f1c;
    --on-green: #ffffff;
    --card-shadow: rgba(0,0,0,0.22);
  }
  * { margin: 0; padding: 0; box-sizing: border-box; }
  html, body { width: 1200px; height: 960px; overflow: hidden; }
  body {
    background: var(--backdrop);
    font-family: "Roboto", Arial, sans-serif;
    position: relative;
  }
  .card {
    position: absolute;
    left: 320px;
    width: 600px;
    height: 344px;
    border-radius: 16px;
    overflow: hidden;
    box-shadow: 0 4px 10px var(--card-shadow);
  }

  /* Reverse side */
  .card--back {
    top: 106px;
    background: var(--brand-green);
  }
  .back-wordmark {
    position: absolute;
    right: 32px;
    bottom: 58px;
    text-align: center;
    color: var(--ink);
  }
  .back-wordmark__name {
    font-family: "Roboto", Arial, sans-serif;
    font-weight: 700;
    font-size: 19px;
    letter-spacing: 0.2px;
  }
  .back-wordmark__tagline {
    font-weight: 500;
    font-size: 14px;
    margin-top: 6px;
  }

  /* Front side */
  .card--front {
    top: 492px;
    background: var(--card-white);
  }
  .front-shapes { position: absolute; inset: 0; }
  .contact {
    position: absolute;
    left: 27px;
    top: 72px;
    color: var(--on-green);
  }
  .contact__name {
    font-family: "Roboto Condensed", Arial, sans-serif;
    font-weight: 700;
    font-size: 21px;
    line-height: 24px;
  }
  .contact__title {
    font-family: "Roboto Condensed", Arial, sans-serif;
    font-size: 15px;
    margin-top: 2px;
  }
  .contact__address {
    font-size: 13.5px;
    line-height: 19px;
    margin-top: 14px;
  }
  .contact__lines {
    list-style: none;
    margin-top: 10px;
    font-size: 13.5px;
    line-height: 19px;
  }
  .contact__lines li { display: flex; align-items: center; }
  .contact__lines svg { width: 13px; height: 13px; margin-right: 10px; fill: var(--on-green); }
  .front-wordmark {
    position: absolute;
    left: 300px;
    width: 300px;
    top: 160px;
    text-align: center;
    font-family: "Roboto", Arial, sans-serif;
    font-weight: 700;
    font-size: 19px;
    color: var(--ink);
  }
</style>
</head>
<body>

  <section class="card card--back" aria-label="Card reverse">
    <div class="back-wordmark">
      <div class="back-wordmark__name">THE STONEBRACE CO.</div>
      <div class="back-wordmark__tagline">Crushing Solutions</div>
    </div>
  </section>

  <section class="card card--front" aria-label="Card front">
    <svg class="front-shapes" viewBox="0 0 600 344" preserveAspectRatio="none" aria-hidden="true">
      <path d="M0 0 H288 C250 90 250 240 300 344 H0 Z" fill="var(--brand-green)"/>
      <path d="M312 0 C262 80 255 220 285 330 C268 220 278 90 318 0 Z" fill="var(--brand-green)"/>
    </svg>

    <div class="contact">
      <div class="contact__name">DALE MORROW</div>
      <div class="contact__title">CEO/FOUNDER</div>
      <div class="contact__address">2218- 48B Avenue<br>Harlow, Alberta T9E 1K2</div>
      <ul class="contact__lines">
        <li><svg viewBox="0 0 16 16"><path d="M3 1l3 3-2 2c1 2 3 4 5 5l2-2 3 3-2 3C6 14 2 10 1 3z"/></svg>780.555.0142</li>
        <li><svg viewBox="0 0 16 16"><path d="M4 0h8v16H4zM5.5 2v10h5V2zM7 13.2h2v1.4H7z" fill-rule="evenodd"/></svg>780.555.0187</li>
        <li><svg viewBox="0 0 16 16"><path d="M4 1h8v4H4zM1 6h14v6h-3v3H4v-3H1zM5 10v4h6v-4z" fill-rule="evenodd"/></svg>780.555.0163</li>
        <li><svg viewBox="0 0 16 16"><path d="M1 3h14v10H1zM2 4l6 5 6-5v-0.2H2z"/></svg>dale@stonebr.com</li>
        <li><svg viewBox="0 0 16 16"><circle cx="8" cy="8" r="7"/></svg>www.stonebrace.ca</li>
      </ul>
    </div>

    <div class="front-wordmark">THE STONEBRACE CO.</div>
  </section>

</body>
</html>
```